Tidewell-Network Theme For Forums!

We are looking for a theme for our forums. The forums are ran off Invision Power Boards. We have a basic theme on there now but we want more our own feel. If possible have some longboarding accept incorporated in the theme. We want the theme to have some red in it to match our logo. Tidewell-network.com

Target Market(s)

Skatingboarding & Longboarding

Coding

Coded - Design and coding required

Number of Pages Required

1 page

Colors
f04a50

```html
<!DOCTYPE html>
<html lang="en">
<head>
<meta charset="utf-8">
<title>Tidewell Network Forums</title>
<link rel="stylesheet" href="https://fonts.googleapis.com/css2?family=Poppins:wght@300;400;500;600;700&display=swap">
<style>
:root{
  --red:#ee0016;
  --red-soft:#f04a50;
  --ink:#1c1c1c;
  --muted:#6f6f6f;
  --pink-head:#f9c9cf;
  --pink-row:#efb8bf;
  --pink-bg:#f7ecef;
  --line:#e8c9ce;
  --white:#ffffff;
  --grey:#dedede;
}
*{box-sizing:border-box;margin:0;padding:0}
html,body{width:1190px;height:1200px;overflow:hidden;background:var(--white);font-family:'Poppins',sans-serif;color:var(--ink)}
.page{position:relative;width:1190px;height:1200px;border-top:4px solid var(--red);border-bottom:4px solid var(--red)}
.abs{position:absolute}
a{color:inherit}
/* header */
.brand{left:85px;top:30px;display:flex;align-items:center;gap:10px}
.brand-mark{width:22px;height:22px;background:var(--red)}
.brand-name{font-weight:700;font-size:22px;color:var(--red);letter-spacing:.5px}
.search{left:418px;top:34px;width:349px;height:34px;border:1px solid #d8d8d8;border-radius:17px;display:flex;align-items:center;justify-content:space-between;padding:0 20px 0 30px;font-size:11px;color:var(--muted);font-weight:300}
.nav{left:786px;top:38px;height:26px;border-left:1px solid #ddd;padding-left:20px;display:flex;gap:34px;font-size:14px;align-items:center}
.nav span{display:flex;align-items:center;gap:6px}
.guest{left:42px;top:99px;width:1106px;height:55px;background:var(--pink-bg);border:1px solid #f1dde1;display:flex;align-items:center;justify-content:center;font-size:15px}
.guest b{font-weight:400;font-size:20px;margin:0 2px}
.title{left:99px;top:185px;border-left:3px solid var(--red);padding-left:11px;font-size:20px;line-height:28px}
.loginbar{left:42px;top:238px;width:1106px;height:54px;border:1px solid #e2c6cb;display:flex;align-items:center;padding:0 23px 0 84px;font-size:13.5px}
.loginbar .msg{flex:1}
.field{width:150px;height:25px;border:1px solid #e2e2e2;margin-right:8px;font-size:11px;padding-left:12px;display:flex;align-items:center;color:#555}
.go{width:42px;height:24px;background:var(--red);color:#fff;font-weight:600;font-size:14px;display:flex;align-items:center;justify-content:center;letter-spacing:1px}
/* panels */
.panel{border:1px solid #e2c6cb}
.panel-head{height:40px;background:var(--red);color:#fff;font-weight:600;font-size:14px;display:flex;align-items:center;justify-content:space-between;padding:0 20px 0 25px}
.collapse{width:13px;height:13px;background:#fff;border-radius:3px;position:relative}
.collapse::after{content:"";position:absolute;left:3px;right:3px;top:6px;height:2px;background:var(--red)}
.tbl{display:grid;grid-template-columns:395px 101px 96px 177px}
.th{height:39px;background:var(--pink-head);display:flex;align-items:center;font-size:14px;border-right:1px solid #e7b1b8}
.td{height:95px;background:var(--pink-bg);border-right:1px solid #e7c9ce;display:flex;align-items:center;font-size:13px}
.th:last-child,.td:last-child{border-right:none}
.center{justify-content:center}
.forumicon{width:32px;height:32px;border-radius:6px;background:#57a845;flex:none}
.lastinfo{flex-direction:column;align-items:flex-start;justify-content:center;padding-left:22px;font-size:12px;gap:6px}
.lastinfo .date{font-size:13px;color:#444}
.lastinfo u{font-size:11.5px}
/* board stats */
.sub{height:38px;background:var(--pink-bg);display:flex;align-items:center;justify-content:center;font-size:13px}
.bar{height:40px;background:var(--pink-row);display:flex;align-items:center;padding-left:26px;font-size:13px;border-top:1px solid #f3d9dc}
.row{display:flex;background:var(--pink-bg)}
.row .ic{width:57px;border-right:1px solid #e2c6cb;display:flex;align-items:center;justify-content:center;flex:none}
.row .tx{padding-left:18px;display:flex;flex-direction:column;justify-content:center;gap:10px;font-size:12px}
.red{color:var(--red)}
/* right */
.mind{height:39px;display:flex;background:var(--pink-bg);font-size:14px}
.mind .q{flex:1;display:flex;align-items:center;padding-left:25px}
.mind .arrow{width:43px;background:#222;display:flex;align-items:center;justify-content:center}
.status{display:flex;gap:16px;padding:0 15px 0 10px;height:107px;align-items:flex-start}
.avatar{width:54px;height:60px;background:var(--grey);flex:none;margin-top:8px}
.status .nm{font-size:13.5px}
.status .bd{font-size:11.5px;color:var(--muted);font-weight:300;line-height:20px;margin-top:2px}
.status .dt,.topic .dt{font-size:10.5px;color:var(--red);text-decoration:underline;margin-top:4px}
.viewall{height:35px;background:var(--pink-bg);border-top:1px solid #ead8db;display:flex;align-items:center;justify-content:center;font-size:11px;text-decoration:underline}
.topic{height:77px;padding:20px 0 0 30px;font-size:14px}
.topic.alt{background:var(--pink-bg)}
.footer{left:0;width:1190px;top:1145px;text-align:center;font-size:13px;color:#444}
</style>
</head>
<body>
<div class="page">
  <div class="abs brand"><div class="brand-mark"></div><div class="brand-name">TIDEWELL NETWORK</div></div>
  <div class="abs search"><span>Search..</span>
    <svg width="12" height="12" viewBox="0 0 12 12"><circle cx="5" cy="5" r="3.8" fill="none" stroke="#777" stroke-width="1.6"/><line x1="8" y1="8" x2="11" y2="11" stroke="#777" stroke-width="1.8"/></svg></div>
  <div class="abs nav">
    <span><svg width="12" height="12"><circle cx="6" cy="6" r="6" fill="#ee0016"/><text x="6" y="9.5" font-size="9" fill="#fff" text-anchor="middle" font-family="Poppins" font-weight="700">?</text></svg>Help</span>
    <span><svg width="16" height="12"><circle cx="8" cy="3" r="2.6" fill="#ee0016"/><circle cx="3" cy="4" r="2" fill="#ee0016"/><circle cx="13" cy="4" r="2" fill="#ee0016"/><rect x="4" y="6" width="8" height="6" rx="3" fill="#ee0016"/><rect x="0" y="7" width="5" height="4" rx="2" fill="#ee0016"/><rect x="11" y="7" width="5" height="4" rx="2" fill="#ee0016"/></svg>Members</span>
    <span><svg width="13" height="13"><rect x="0.5" y="2" width="12" height="10.5" fill="none" stroke="#ee0016"/><rect x="0.5" y="2" width="12" height="3" fill="#ee0016"/><g fill="#ee0016"><rect x="2.5" y="7" width="2" height="2"/><rect x="5.5" y="7" width="2" height="2"/><rect x="8.5" y="7" width="2" height="2"/></g></svg>Calendar</span>
  </div>

  <div class="abs guest">WELCOME GUEST <b>(</b> Login | Register <b>)</b></div>
  <div class="abs title">TIDEWELL NETWORK</div>
  <div class="abs loginbar"><span class="msg">Welcome Back;your last visit was : Today,01/06/2017</span>
    <div class="field">User Name</div><div class="field">••••••••••••••••••••••••</div><div class="go">GO</div></div>

  <!-- forum table -->
  <div class="abs panel" style="left:42px;top:326px;width:771px">
    <div class="panel-head">A Test Root<div class="collapse"></div></div>
    <div class="tbl">
      <div class="th" style="padding-left:25px">Forum</div>
      <div class="th center">Topics</div>
      <div class="th center">Replies</div>
      <div class="th" style="padding-left:22px">Last Post Info</div>
      <div class="td" style="padding-left:25px;gap:17px"><div class="forumicon"></div>
        <div><div style="font-size:13.5px">A Test Forum</div><div style="color:var(--muted);margin-top:6px">A Test Forum that may be removed at any time</div></div></div>
      <div class="td center">1</div>
      <div class="td center">1</div>
      <div class="td lastinfo"><div class="date">▣ Apr 7 2006,07:52 PM</div><div>In : <u>Welcome!</u></div><div>Out : <u>Core Team</u></div></div>
    </div>
  </div>

  <!-- board stats -->
  <div class="abs panel" style="left:42px;top:539px;width:771px">
    <div class="panel-head">Board Statistics<div class="collapse"></div></div>
    <div class="sub">Today's active topics.The moderating team.Today's top Posters.Overall top 10 posters</div>
    <div class="bar">2 User(s) active in the past 15 minutes</div>
    <div class="row" style="height:71px"><div class="ic"><div role="img" aria-label="Online user icon" style="width:35px;height:35px;border-radius:50%;background:#2e8fd8"></div></div>
      <div class="tx"><div>2 Guests,0 members 0 anonymous &nbsp;members</div><div><b class="red" style="font-weight:600">Show Detailed by :</b> <u>Last Click</u>,<u>Member name</u></div></div></div>
    <div class="bar">A Second Test Forum</div>
    <div class="row" style="height:71px"><div class="ic"><div class="forumicon" style="width:38px;height:38px"></div></div>
      <div class="tx">Sed ut perspiciatis unde omnis iste natus error sit voluptatem</div></div>
    <div class="bar">Forthcoming Calendar Events within the next 5 days</div>
    <div class="row" style="height:71px"><div class="ic">
      <svg width="40" height="40" viewBox="0 0 40 40"><rect x="1" y="5" width="38" height="34" rx="4" fill="#dfe3ea"/><rect x="1" y="5" width="38" height="10" rx="4" fill="#e8343c"/><g fill="#8d95a6"><rect x="8" y="19" width="5" height="4"/><rect x="15" y="19" width="5" height="4"/><rect x="22" y="19" width="5" height="4"/><rect x="29" y="19" width="4" height="4"/><rect x="8" y="26" width="5" height="4"/><rect x="15" y="26" width="5" height="4"/><rect x="22" y="26" width="5" height="4"/><rect x="29" y="26" width="4" height="4"/></g><rect x="10" y="1" width="3" height="8" rx="1.5" fill="#555"/><rect x="27" y="1" width="3" height="8" rx="1.5" fill="#555"/></svg></div>
      <div class="tx">There is no Forthcoming Calendar Events</div></div>
    <div class="bar" style="font-weight:600">Board Statistics</div>
    <div class="row" style="height:99px"><div class="ic">
      <svg width="38" height="38" viewBox="0 0 38 38"><circle cx="19" cy="19" r="19" fill="#2d3a4a"/><rect x="10" y="17" width="5" height="13" fill="#f2b632"/><rect x="17" y="10" width="5" height="20" fill="#e8343c"/><rect x="24" y="20" width="5" height="10" fill="#48b07b"/></svg></div>
      <div class="tx" style="gap:8px"><div>Our Members have made a total of <span class="red">1 posts</span></div><div>We have <span class="red">1 Registered</span> members</div><div>The Newest Member is <span class="red">Admin</span></div></div></div>
  </div>

  <!-- status updates -->
  <div class="abs panel" style="left:837px;top:326px;width:312px">
    <div class="panel-head">Recent Status Updates<div class="collapse"></div></div>
    <div class="mind"><div class="q">What is your mind?</div><div class="arrow"><svg width="18" height="10"><line x1="0" y1="5" x2="15" y2="5" stroke="#fff" stroke-width="2"/><path d="M12 1 L17 5 L12 9" fill="none" stroke="#fff" stroke-width="2"/></svg></div></div>
    <div style="height:13px"></div>
    <div class="status"><div class="avatar" role="img" aria-label="Member avatar placeholder"></div>
      <div><div class="nm">Nemo enim</div><div class="bd">Sed ut perspiciatis unde omni istenat userror sit.</div><div class="dt">Jun 1 2018 &nbsp;5:20 PM</div></div></div>
    <div class="status"><div class="avatar" role="img" aria-label="Member avatar placeholder"></div>
      <div><div class="nm">Nemo enim</div><div class="bd">Sed ut perspiciatis unde omni istenat userror sit.</div><div class="dt">Jun 1 2018 &nbsp;5:20 PM</div></div></div>
    <div class="viewall">View All Updates &nbsp;»</div>
  </div>

  <!-- recent topics -->
  <div class="abs panel" style="left:837px;top:717px;width:312px">
    <div class="panel-head">Recently Added Topics<div class="collapse"></div></div>
    <div class="topic">Nemo enim ipsam voluptatem<div class="dt">Jun 1 2018 &nbsp;5:20 PM</div></div>
    <div class="topic alt">Nemo enim ipsam voluptatem<div class="dt">Jun 1 2018 &nbsp;5:20 PM</div></div>
    <div class="topic">Nemo enim ipsam voluptatem<div class="dt">Jun 1 2018 &nbsp;5:20 PM</div></div>
    <div class="topic alt">Nemo enim ipsam voluptatem<div class="dt">Jun 1 2018 &nbsp;5:20 PM</div></div>
  </div>

  <div class="abs footer">© Copyright 2018 Tidewell Network.All Rights Reserved</div>
</div>
</body>
</html>
```